Silver Bloom Marisol's Cleaning Service Business Cards Project

A business card with all contact details with logo design on there (already have a logo) eye catching Logo and contact info on one side, full logo on the back, must target upper class residential and corporate companies, fitness companies, still keep it on the feminine side of things , must look elegant

Target Market(s)

Upper class homes and corporate companies

Industry/Entity Type

Cleaning Service

Contact Information for Business Card

Name: Marisol Quenby
Position: Director
ABN: 31647209853
Email: marisolssilvercleaning@tidymail.example
Number: 0417906354

Font styles to use
Decorative

Colors

Designer to choose colors to be used in the design.

Requirements
Must have
• Available Sydney Wide, contact info and logo on one side, full logo on the back
Nice to have
• Professional appearance
Should not have
• Cheap advert looking stuff

```html
<!DOCTYPE html>
<html lang="en">
<head>
<meta charset="utf-8">
<title>Silver Bloom Business Cards</title>
<link rel="stylesheet" href="https://fonts.googleapis.com/css2?family=Roboto:wght@400;500;700&display=swap">
<style>
  :root {
    --backdrop: #e9e7e3;
    --card-front: #18191b;
    --card-back: #2d313d;
    --aqua-light: #97fbf7;
    --aqua: #2ce5d9;
    --teal-text: #34e0d8;
    --ornament-start: rgba(52, 224, 216, 0.10);
    --ornament-mid: rgba(52, 224, 216, 0.32);
    --white: #ffffff;
    --divider: #3a3c40;
  }
  * { margin: 0; padding: 0; box-sizing: border-box; }
  html, body {
    width: 1200px; height: 960px; overflow: hidden;
    background: var(--backdrop);
    font-family: "Roboto", Arial, sans-serif;
  }
  .canvas { position: relative; width: 1200px; height: 960px; }

  .card {
    position: absolute; width: 600px; height: 343px;
    box-shadow: 0 4px 10px rgba(0,0,0,0.25);
    overflow: hidden;
  }
  .card-front { left: 314px; top: 113px; background: var(--card-front); }
  .card-back { left: 311px; top: 472px; background: var(--card-back); }

  .band-top { position: absolute; left: 0; top: 0; width: 100%; height: 32px; background: var(--aqua-light); }
  .band-bottom { position: absolute; left: 0; bottom: 0; width: 100%; height: 26px; background: var(--aqua); }

  .brand-mark {
    position: absolute; border: 2px solid var(--teal-text); border-radius: 50%;
  }
  .ornament {
    position: absolute; border-radius: 20px;
    background: linear-gradient(90deg, var(--ornament-start), var(--ornament-mid) 50%, var(--ornament-start));
  }

  .brand {
    position: absolute; text-align: center; color: var(--teal-text);
    font-weight: 500; line-height: 1.2;
  }
  .brand-name { display: block; letter-spacing: 1px; text-transform: uppercase; }
  .brand-tagline { display: block; letter-spacing: 2px; text-transform: uppercase; }

  .card-front .brand-mark { left: 116px; top: 86px; width: 56px; height: 56px; }
  .card-front .ornament { left: 48px; top: 150px; width: 190px; height: 38px; }
  .card-front .brand { left: 30px; top: 195px; width: 226px; }
  .card-front .brand-name { font-size: 20px; }
  .card-front .brand-tagline { font-size: 8.5px; margin-top: 6px; }

  .divider {
    position: absolute; left: 266px; top: 82px; width: 1px; height: 160px;
    background: var(--divider);
  }

  .contact { position: absolute; left: 297px; top: 89px; color: var(--white); }
  .contact-name { font-size: 20px; font-weight: 700; color: var(--teal-text); letter-spacing: 0.3px; }
  .contact-role { font-size: 14px; font-weight: 500; color: var(--teal-text); margin-top: 1px; }
  .contact-abn { font-size: 14px; margin-top: 14px; }
  .contact-list { list-style: none; margin-top: 12px; }
  .contact-list li {
    display: flex; align-items: center; gap: 8px;
    font-size: 14px; line-height: 19px;
  }
  .contact-list svg { width: 12px; height: 12px; flex: none; }

  .card-back .brand-mark { left: 260px; top: 78px; width: 70px; height: 70px; }
  .card-back .ornament { left: 183px; top: 155px; width: 224px; height: 45px; }
  .card-back .brand { left: 0; top: 206px; width: 100%; }
  .card-back .brand-name { font-size: 25px; }
  .card-back .brand-tagline { font-size: 10px; margin-top: 6px; }
  .back-web {
    position: absolute; left: 0; top: 290px; width: 100%; text-align: center;
    color: var(--white); font-size: 14px; letter-spacing: 4px;
  }
</style>
</head>
<body>
<main class="canvas">
  <section class="card card-front">
    <div class="band-top"></div>
    <div class="brand-mark" aria-hidden="true"></div>
    <div class="ornament" role="img" aria-label="Decorative floral flourish beneath the brand name"></div>
    <div class="brand">
      <span class="brand-name">Silver Bloom</span>
      <span class="brand-tagline">Marisol's Cleaning Service</span>
    </div>
    <div class="divider"></div>
    <div class="contact">
      <div class="contact-name">MARISOL QUENBY</div>
      <div class="contact-role">DIRECTOR</div>
      <div class="contact-abn">ABN: 31647209853</div>
      <ul class="contact-list">
        <li>
          <svg viewBox="0 0 12 12" aria-hidden="true"><path fill="#34e0d8" d="M2.4 0.6l2 2.1-1 1.4c.7 1.6 2 2.9 3.6 3.6l1.4-1 2.1 2-1.1 2.1C4.4 10.6 1.4 7.6 0.3 1.7z"/></svg>
          <span>0417906354</span>
        </li>
        <li>
          <svg viewBox="0 0 12 12" aria-hidden="true"><rect x="0.5" y="2" width="11" height="8" fill="#34e0d8"/><path d="M0.5 2.3L6 6.6l5.5-4.3" fill="none" stroke="#18191b" stroke-width="1"/></svg>
          <span>marisolssilvercleaning@tidymail.example</span>
        </li>
        <li>
          <svg viewBox="0 0 12 12" aria-hidden="true"><circle cx="6" cy="6" r="5.5" fill="#34e0d8"/><path d="M0.8 6h10.4M6 0.5c-2.4 3-2.4 8 0 11M6 0.5c2.4 3 2.4 8 0 11" fill="none" stroke="#18191b" stroke-width="0.8"/></svg>
          <span>www.silverbloom.example</span>
        </li>
      </ul>
    </div>
    <div class="band-bottom"></div>
  </section>

  <section class="card card-back">
    <div class="brand-mark" aria-hidden="true"></div>
    <div class="ornament" role="img" aria-label="Decorative floral flourish beneath the brand name"></div>
    <div class="brand">
      <span class="brand-name">Silver Bloom</span>
      <span class="brand-tagline">Marisol's Cleaning Service</span>
    </div>
    <div class="back-web">www.silverbloom.example</div>
  </section>
</main>
</body>
</html>
```